New business card for a regional office of a US M&A company

We need business card for a finance company, office based in Hong Kong , our Head office is in US, our business is to Merge and acquires companies , the new office will be a regional office for the Asia Pacific region. We want to use the head office logo as attached ( but don't have to be exactly the same, can be a variation to it) as a base and then add Asia Pacific alongside the logo.
We would prefer to have be bilingual Eng + Chinese, although we don't really have Chinese company name .

Industry/Entity Type

Business

Contact Information for Business Card

Clara Jo Tsang
 

VP,
APAC M&A Operations
Orin Vantage Asia Pacific Limited
 
Unit 1407, K18
18 Tai Lok Shan Road, 
Hong Kong 
 
M: +852 6038 1742
T : +852 2836 4100
F : +852 2836 4177
VOIP: 4158
 
cjtsang@orinvantage.com

Font styles to use
Serif
Sans Serif

Colors

Designer to choose colors to be used in the design.

Requirements
Must have
• APAC Office

```html
<!DOCTYPE html>
<html lang="en">
<head>
<meta charset="utf-8">
<title>Orin Vantage – Business Card</title>
<link rel="stylesheet" href="https://fonts.googleapis.com/css2?family=Open+Sans:wght@700&family=Roboto+Condensed:wght@700&family=Roboto:wght@400&display=swap">
<style>
  :root {
    --navy: #0f2944;
    --cyan: #1ca9d1;
    --paper: #eceff2;
    --white: #ffffff;
    --ink-grey: #4a4f55;
    --stage: #d9dde1;
    --rule: #c9d3dc;
  }
  * { margin: 0; padding: 0; box-sizing: border-box; }
  html, body { width: 1200px; height: 960px; overflow: hidden; }
  body { background: var(--stage); position: relative; font-family: "Roboto", sans-serif; }

  .card { position: absolute; width: 600px; height: 343px; overflow: hidden; }

  /* Front */
  .card-front { left: 314px; top: 113px; background: var(--navy); color: var(--white); }
  .brand-front {
    position: absolute; right: 36px; top: 112px;
    font-family: "Open Sans", sans-serif; font-weight: 700; font-size: 36px;
    color: var(--cyan); letter-spacing: 0.5px; line-height: 1;
  }
  .holder-name {
    position: absolute; left: 34px; top: 163px;
    font-family: "Roboto Condensed", sans-serif; font-weight: 700; font-size: 21px;
    color: var(--cyan); line-height: 1;
  }
  .holder-title { position: absolute; left: 36px; top: 190px; font-size: 14px; line-height: 1; }
  .divider { position: absolute; left: 58px; right: 37px; top: 198px; height: 1px; background: var(--rule); }
  .contact-list { position: absolute; left: 36px; top: 213px; list-style: none; font-size: 14px; }
  .contact-list li { display: flex; align-items: center; height: 19px; }
  .contact-list svg { width: 14px; height: 14px; margin-right: 8px; fill: var(--cyan); }
  .voip { position: absolute; left: 35px; top: 277px; font-size: 14px; }
  .address {
    position: absolute; right: 38px; top: 207px; text-align: right;
    font-size: 14px; line-height: 18.6px; font-style: normal;
  }
  .accent-band { position: absolute; left: 0; bottom: 0; width: 330px; height: 13px; background: var(--cyan); }
  .corner-panel { position: absolute; right: 0; bottom: 0; width: 280px; height: 34px; }

  /* Back */
  .card-back { left: 311px; top: 472px; background: var(--paper); box-shadow: 0 1px 3px rgba(0,0,0,0.15); }
  .brand-back {
    position: absolute; left: 0; right: 0; top: 186px; text-align: center;
    font-family: "Open Sans", sans-serif; font-weight: 700; font-size: 46px;
    color: var(--cyan); line-height: 1;
  }
  .web-address {
    position: absolute; left: 0; right: 0; top: 285px; text-align: center;
    font-size: 14px; letter-spacing: 0.55em; color: var(--ink-grey);
  }
</style>
</head>
<body>

<section class="card card-front">
  <div class="brand-front">ORIN VANTAGE</div>

  <div class="holder-name">CLARA JO TSANG</div>
  <div class="holder-title">VP</div>
  <div class="divider"></div>

  <ul class="contact-list">
    <li>
      <svg viewBox="0 0 24 24" aria-hidden="true"><path d="M6.6 10.8a15 15 0 0 0 6.6 6.6l2.2-2.2c.3-.3.7-.4 1-.2 1.1.4 2.3.6 3.6.6.6 0 1 .4 1 1V20c0 .6-.4 1-1 1A17 17 0 0 1 3 4c0-.6.4-1 1-1h3.5c.6 0 1 .4 1 1 0 1.3.2 2.5.6 3.6.1.3 0 .7-.2 1z"/></svg>
      +852 2836 4100
    </li>
    <li>
      <svg viewBox="0 0 24 24" aria-hidden="true"><path d="M7 1h10a2 2 0 0 1 2 2v18a2 2 0 0 1-2 2H7a2 2 0 0 1-2-2V3a2 2 0 0 1 2-2zm0 3v15h10V4zm5 16.2a1 1 0 1 0 0 .1z"/></svg>
      +852 6038 1742
    </li>
    <li>
      <svg viewBox="0 0 24 24" aria-hidden="true"><path d="M6 2h12v6H6zM3 9h18a1 1 0 0 1 1 1v8h-4v4H6v-4H2v-8a1 1 0 0 1 1-1zm5 7v4h8v-4z"/></svg>
      +852 2836 4177
    </li>
  </ul>
  <div class="voip">VOIP: 4158</div>

  <address class="address">
    APAC M&amp;A Operations<br>
    Orin Vantage Asia Pacific Limited<br>
    Unit 1407, K18<br>
    18 Tai Lok Shan Road<br>
    Hong Kong
  </address>

  <div class="accent-band"></div>
  <svg class="corner-panel" viewBox="0 0 280 34" preserveAspectRatio="none" aria-hidden="true">
    <polygon points="22,0 280,0 280,34 0,34" fill="var(--paper)"/>
  </svg>
</section>

<section class="card card-back">
  <div class="brand-back">ORIN VANTAGE</div>
  <div class="web-address">www.orinvantage.com</div>
</section>

</body>
</html>
```